Business Card Design for a Software Startup

We'd like to have a business card design. We already have a logo. Basically what we need is a clean design with name, address, cellphone and phone numbers, e-mail and web site address (front) and a space on the back with our logo with the company name on the right side and some texts on the bottom.
We are a development and consulting company in Brazil with highly qualified team of professionals in Java, iOS and Android development and consulting.

Target Market(s)

CIO, IT managers of mid to big size companies

Industry/Entity Type

Business

```html
<!DOCTYPE html>
<html lang="en">
<head>
<meta charset="UTF-8">
<title>Vorqel Business Card</title>
<link href="https://fonts.googleapis.com/css2?family=Montserrat:wght@400;500;600;700&display=swap" rel="stylesheet">
<style>
  :root {
    --bg: #ece9e4;
    --navy: #123a67;
    --navy-deep: #0d2c52;
    --navy-soft: #1c4f86;
    --sky: #1f9ad8;
    --sky-light: #5bc0ec;
    --white: #ffffff;
    --grey: #5a6470;
    --shadow: rgba(20, 30, 45, 0.18);
  }
  * { box-sizing: border-box; margin: 0; padding: 0; }
  html, body { width: 1200px; height: 720px; overflow: hidden; }
  body {
    background: var(--bg);
    font-family: "Montserrat", Arial, sans-serif;
    position: relative;
  }
  .card {
    position: absolute;
    top: 200px;
    width: 560px;
    height: 320px;
    border-radius: 6px;
    overflow: hidden;
    box-shadow: 0 10px 28px var(--shadow);
  }
  .card-front { left: 30px; background: var(--white); }
  .card-back {
    left: 610px;
    background: radial-gradient(ellipse at 55% 40%, var(--navy-soft) 0%, var(--navy) 55%, var(--navy-deep) 100%);
  }
  .front-art { position: absolute; inset: 0; width: 100%; height: 100%; }

  .brand {
    position: absolute;
    top: 38px;
    left: 34px;
    display: flex;
    align-items: center;
    gap: 14px;
  }
  .brand-square {
    width: 52px; height: 52px;
    border-radius: 8px;
    background: var(--navy-soft);
  }
  .brand-name {
    font-weight: 700;
    font-size: 50px;
    letter-spacing: 1px;
    color: var(--navy);
    line-height: 1;
  }

  .holder { position: absolute; left: 48px; top: 196px; }
  .holder-name { font-weight: 700; font-size: 19px; color: var(--navy); }
  .holder-title { font-size: 14px; color: var(--grey); margin-top: 2px; }

  .contact-list {
    position: absolute;
    right: 24px;
    top: 96px;
    list-style: none;
    color: var(--white);
    font-size: 13px;
    line-height: 23px;
  }
  .contact-list li { display: flex; align-items: center; gap: 8px; justify-content: flex-end; }
  .contact-list svg { width: 12px; height: 12px; fill: var(--white); flex: none; }

  .address {
    position: absolute;
    right: 24px;
    bottom: 50px;
    color: var(--white);
    font-size: 12.5px;
    transform: rotate(-3deg);
    transform-origin: right bottom;
  }

  .back-square {
    position: absolute;
    left: 190px; top: 50px;
    width: 220px; height: 220px;
    border-radius: 28px;
    background: rgba(255, 255, 255, 0.07);
  }
  .back-name {
    position: absolute;
    left: 0; right: 0; top: 106px;
    text-align: center;
    font-weight: 700;
    font-size: 80px;
    letter-spacing: 2px;
    color: var(--white);
    line-height: 1;
  }
  .back-web {
    position: absolute;
    left: 0; right: 0; top: 232px;
    text-align: center;
    font-weight: 600;
    font-size: 18px;
    letter-spacing: 5px;
    color: var(--white);
  }
</style>
</head>
<body>
  <section class="card card-front">
    <svg class="front-art" viewBox="0 0 560 320" preserveAspectRatio="none" aria-hidden="true">
      <path d="M0,320 L0,296 C160,292 240,252 290,175 C340,95 420,52 560,42 L560,320 Z" fill="var(--navy)"/>
      <path d="M0,286 C160,282 232,244 280,170 C330,88 412,42 560,30 L560,36 C416,48 336,94 286,173 C236,250 160,288 0,292 Z" fill="var(--sky)"/>
      <path d="M262,190 C316,100 396,46 560,24" stroke="var(--sky-light)" stroke-width="2" fill="none"/>
      <path d="M0,262 C120,262 200,246 250,214" stroke="var(--sky)" stroke-width="4" fill="none"/>
      <path d="M0,304 L560,304 L560,320 L0,320 Z" fill="var(--navy-deep)"/>
      <path d="M0,300 C150,300 260,290 560,296 L560,302 C260,296 150,306 0,306 Z" fill="var(--sky)"/>
    </svg>

    <div class="brand">
      <span class="brand-square"></span>
      <span class="brand-name">VORQEL</span>
    </div>

    <div class="holder">
      <p class="holder-name">Your Name</p>
      <p class="holder-title">Title</p>
    </div>

    <ul class="contact-list">
      <li>
        <svg viewBox="0 0 24 24"><path d="M6.6 10.8a15 15 0 0 0 6.6 6.6l2.2-2.2c.3-.3.7-.4 1-.2 1.1.4 2.3.6 3.6.6.6 0 1 .4 1 1V20c0 .6-.4 1-1 1A17 17 0 0 1 3 4c0-.6.4-1 1-1h3.5c.6 0 1 .4 1 1 0 1.3.2 2.5.6 3.6.1.3 0 .7-.2 1z"/></svg>
        555-010-2468
      </li>
      <li>
        <svg viewBox="0 0 24 24"><path d="M7 1h10a2 2 0 0 1 2 2v18a2 2 0 0 1-2 2H7a2 2 0 0 1-2-2V3a2 2 0 0 1 2-2zm0 3v14h10V4z"/></svg>
        555-019-7531
      </li>
      <li>
        <svg viewBox="0 0 24 24"><path d="M2 5h20v14H2zm2 2v.5l8 5 8-5V7zm0 2.8V17h16V9.8l-8 5z"/></svg>
        yourname@vorqel.com
      </li>
      <li>
        <svg viewBox="0 0 24 24"><path d="M12 2a10 10 0 1 0 0 20 10 10 0 0 0 0-20zm6.9 9h-3a15 15 0 0 0-1.3-5.6A8 8 0 0 1 18.9 11zM12 4c.9 1.2 1.7 3.6 1.9 7h-3.8c.2-3.4 1-5.8 1.9-7zM9.4 5.4A15 15 0 0 0 8.1 11h-3a8 8 0 0 1 4.3-5.6zM5.1 13h3a15 15 0 0 0 1.3 5.6A8 8 0 0 1 5.1 13zm6.9 7c-.9-1.2-1.7-3.6-1.9-7h3.8c-.2 3.4-1 5.8-1.9 7zm2.6-1.4a15 15 0 0 0 1.3-5.6h3a8 8 0 0 1-4.3 5.6z"/></svg>
        www.vorqel.com
      </li>
    </ul>

    <p class="address">Door No. Street Name City Name, State, Zip Code</p>
  </section>

  <section class="card card-back">
    <span class="back-square"></span>
    <p class="back-name">VORQEL</p>
    <p class="back-web">www.vorqel.com</p>
  </section>
</body>
</html>
```